Business Card Design - Photographer

I am a landscape photographer and I require a business card design. 

I require two designs:
1)  a double sided business card
 and
b)  a single sided business card 

The single sided design can either be the same as the double sided (with just one side having all the information)....or it can be an entire new design. Its up to you.

My corporate colours are (CMYK):

Blue   69, 32, 0, 0
Grey  72,  64,  47,  31
Green  32,  2,  91,  0
Yellow   0, 19, 92, 0
Orange  0, 39, 75, 0

Colour space in final file should be in CMYK.

The details that need to be included on the card:

- Use the provided Logo
- Name: Wiktor Baranowski
- Email:   sales@vistalumeworks.com.au
- Website:    vistalumeworks.com.au
- Twitter:    twitter.com/vistalumeworks
- Facebook:   facebook.com/vistalumeworks
- Mobile  0417 539 662

Please use the attached template to design the logo to the specified size, including the marked bleed lines. I have also attached my logo in PNG (transparent background) and ai format for you to use.

The final file should be:
- Photoshop version with layers so I can edit the name/text etc. All non vector files should be high resolution at 1039 x 697 pixels at 300 dpi.

I also require a file as:
- Vector based PDF

Anyway questions please contact me.

Thank you

Industry/Entity Type

Landscape

Logo styles of interest
Pictorial/Combination Logo
Abstract Logo
Wordmark Logo
Lettermark Logo
Requirements
Must have
• The details that need to be included on the card:

- Use the provided Logo
- Name: Wiktor Baranowski
- Email: sales@vistalumeworks.com.au
- Website: vistalumeworks.com.au
- Twitter: twitter.com/vistalumeworks
- Facebook: facebook.com/vistalumeworks
- Mobile 0417 539 662

```html
<!DOCTYPE html>
<html lang="en">
<head>
<meta charset="utf-8">
<title>Vistalume Works business cards</title>
<link rel="stylesheet" href="https://fonts.googleapis.com/css2?family=Cinzel:wght@500&family=Arimo:wght@400;700&display=swap">
<style>
  :root {
    --board: #a8811f;
    --card: #ffffff;
    --ink: #3d4052;
    --text: #222222;
    --brand-orange: #f7a44a;
    --social-blue: #3b5998;
    --social-sky: #55acee;
    --white: #ffffff;
  }
  * { margin: 0; padding: 0; box-sizing: border-box; }
  html, body { width: 1200px; height: 686px; overflow: hidden; }
  body { background: var(--board); position: relative; font-family: "Arimo", Arial, sans-serif; }

  .card {
    position: absolute;
    width: 451px; height: 257px;
    background: var(--card);
    border-radius: 21px;
    overflow: hidden;
    box-shadow: 0 2px 4px rgba(0,0,0,.35);
  }
  .card--contact { left: 110px; top: 80px; }
  .card--web { left: 616px; top: 80px; }
  .card--brand { left: 364px; top: 374px; }

  .brand-mark {
    position: absolute;
    width: 82px; height: 82px;
    border-radius: 50%;
    background: var(--ink);
    left: 50%; transform: translateX(-50%);
  }
  .brand-name {
    position: absolute; left: 0; right: 0;
    text-align: center;
    font-family: "Cinzel", "Times New Roman", serif;
    font-weight: 500;
    font-size: 22px;
    letter-spacing: .5px;
    color: var(--ink);
    white-space: nowrap;
  }
  .card--contact .brand-mark { top: 16px; }
  .card--contact .brand-name { top: 110px; }
  .card--web .brand-mark { top: 29px; }
  .card--web .brand-name { top: 132px; }
  .card--brand .brand-mark { top: 65px; }
  .card--brand .brand-name { top: 161px; }

  .contact-row {
    position: absolute; left: 0; right: 0;
    display: flex; justify-content: center; gap: 14px;
    font-size: 12px; color: var(--text);
    white-space: nowrap;
  }
  .contact-row--primary { top: 160px; padding-left: 18px; }
  .contact-row--social { top: 179px; padding-left: 6px; gap: 16px; }
  .contact-item { display: flex; align-items: center; gap: 3px; }
  .contact-item svg { display: block; }
  .social-square { width: 13px; height: 13px; display: inline-block; }
  .social-square--fb { background: var(--social-blue); }
  .social-square--tw { background: var(--social-sky); }

  .wave { position: absolute; left: 0; top: 0; width: 451px; height: 257px; }
  .website {
    position: absolute; right: 30px; top: 231px;
    font-weight: 700; font-size: 12px; line-height: 14px;
    color: var(--white); white-space: nowrap;
  }
</style>
</head>
<body>
  <svg width="0" height="0" style="position:absolute">
    <defs>
      <linearGradient id="stripe" x1="0" x2="1" y1="0" y2="0">
        <stop offset="0" stop-color="#3f8fd8"/>
        <stop offset=".18" stop-color="#8cc63f"/>
        <stop offset=".5" stop-color="#ffd000"/>
        <stop offset=".8" stop-color="#b3d335"/>
        <stop offset="1" stop-color="#3aa3c8"/>
      </linearGradient>
      <linearGradient id="band" x1="0" x2="1" y1="0" y2="0">
        <stop offset="0" stop-color="#1c1f2c"/>
        <stop offset=".45" stop-color="#4b4e63"/>
        <stop offset="1" stop-color="#2b2e3f"/>
      </linearGradient>
    </defs>
  </svg>

  <section class="card card--contact">
    <div class="brand-mark"></div>
    <div class="brand-name">Vistalume Works</div>
    <div class="contact-row contact-row--primary">
      <span class="contact-item">
        <svg width="10" height="12" viewBox="0 0 10 12"><path d="M2 0 L4 3 L3 4.5 C3.5 6.5 4.5 7.8 6 8.5 L7.3 7.5 L10 9.5 L8.5 11.8 C4 11 1 7 0.5 2 Z" fill="var(--brand-orange)"/></svg>
        0417 539 662
      </span>
      <span class="contact-item">
        <svg width="14" height="10" viewBox="0 0 14 10"><rect x=".5" y=".5" width="13" height="9" fill="var(--brand-orange)"/><path d="M.5 .5 L7 5.5 L13.5 .5" fill="none" stroke="#fff" stroke-width="1"/></svg>
        sales@vistalumeworks.com.au
      </span>
    </div>
    <div class="contact-row contact-row--social">
      <span class="contact-item"><span class="social-square social-square--fb"></span>@vistalumeworks</span>
      <span class="contact-item"><span class="social-square social-square--tw"></span>@vistalumeworks</span>
    </div>
    <svg class="wave" viewBox="0 0 451 257" aria-hidden="true">
      <path d="M0 197 C80 201 150 219 230 219 C310 219 380 196 451 190 L451 206 C380 210 310 222 230 223 C150 224 70 217 0 211 Z" fill="url(#stripe)"/>
      <path d="M0 214 C70 220 150 227 230 226 C310 225 380 213 451 209 L451 257 L0 257 Z" fill="url(#band)"/>
    </svg>
    <div class="website">www.vistalumeworks.com.au</div>
  </section>

  <section class="card card--web">
    <div class="brand-mark"></div>
    <div class="brand-name">Vistalume Works</div>
    <svg class="wave" viewBox="0 0 451 257" aria-hidden="true">
      <path d="M0 197 C80 201 150 219 230 219 C310 219 380 196 451 190 L451 206 C380 210 310 222 230 223 C150 224 70 217 0 211 Z" fill="url(#stripe)"/>
      <path d="M0 214 C70 220 150 227 230 226 C310 225 380 213 451 209 L451 257 L0 257 Z" fill="url(#band)"/>
    </svg>
    <div class="website">www.vistalumeworks.com.au</div>
  </section>

  <section class="card card--brand">
    <div class="brand-mark"></div>
    <div class="brand-name">Vistalume Works</div>
  </section>
</body>
</html>
```